Stationery Design Project

I need a stationary design for our company. we are based in Houston, TX and we are called Mira Vell Lending. And we are wanting to brand our MoneyMendPlus program, which includes our tax preparation and restoration, credit repair service. Although our business offers other programs, we are interested in mainly focusing on The MoneyMendPlus program. We are looking for way to brand our ourselves and I believe that a great stationery design will help in achieving this goal. Our logo design is blue and light blue. the slogan is orange.

Industry/Entity Type

Business

Requirements
Must have
• Address: 30871 Calloway Ln. B-22
Houston, TX 75419
Tel. 555-318-6207
Fax 555-294-7153
www.miravelllending.example
info@miravelllending.example
Our Slogan: Balance, Renewed!

```html
<!DOCTYPE html>
<html lang="en">
<head>
<meta charset="utf-8">
<title>Mira Vell Lending — Business Card</title>
<link rel="stylesheet" href="https://fonts.googleapis.com/css2?family=Cinzel:wght@600&family=Libre+Baskerville&family=Source+Sans+3:wght@400;600&display=swap">
<style>
  :root {
    --navy: #123d66;
    --navy-deep: #0e2f52;
    --blue: #1f6fb0;
    --sky: #2e8fd0;
    --pale: #d2e6f5;
    --orange: #f39a22;
    --ink: #222;
    --paper: #ffffff;
    --stage: #e9e6e2;
  }
  html, body { margin: 0; padding: 0; overflow: hidden; }
  body {
    width: 1200px; height: 800px; position: relative;
    background: var(--stage);
    font-family: "Source Sans 3", Arial, sans-serif;
  }
  .label {
    position: absolute; width: 300px; text-align: center;
    font-size: 21px; color: var(--ink);
  }
  .card {
    position: absolute; width: 508px; height: 290px;
    border-radius: 18px; overflow: hidden;
    box-shadow: 0 4px 12px rgba(0,0,0,.25);
  }
  .card--light { background: var(--paper); }
  .card--dark { background: var(--navy); }

  /* Front */
  .front__wave { position: absolute; left: 0; top: 0; }
  .front__brand {
    position: absolute; left: 26px; top: 124px;
    font-weight: 600; font-size: 32px; color: var(--blue); letter-spacing: -.3px;
  }
  .front__divider {
    position: absolute; left: 268px; top: 34px;
    width: 1px; height: 140px; background: #cfcfcf;
  }
  .front__contact {
    position: absolute; left: 288px; top: 62px;
    margin: 0; padding: 0; list-style: none;
    font-size: 14px; color: #333; line-height: 23px;
  }
  .front__contact b { font-style: italic; font-weight: 600; }
  .front__address {
    position: absolute; left: 17px; top: 238px;
    font-size: 14px; color: #fff; line-height: 18px; font-style: normal;
  }

  /* Backs */
  .slogan {
    position: absolute; left: 0; right: 0; top: 22px;
    text-align: center; font-family: "Cinzel", Georgia, serif;
    font-weight: 600; font-size: 19px; color: var(--orange);
  }
  .url {
    position: absolute; left: 0; right: 0; bottom: 20px;
    text-align: center; font-size: 21px; letter-spacing: 2px;
  }
  .card--light .url { color: #333; }
  .card--dark .url { color: #fff; bottom: 14px; }
  .name { font-family: "Libre Baskerville", Georgia, serif; color: #fff; }
  .badge {
    position: absolute; left: 168px; top: 58px;
    width: 170px; height: 170px; box-sizing: border-box;
    display: flex; align-items: center; justify-content: center;
    text-align: center;
  }
  .badge--outlined { border: 1px solid #9cbcd8; padding: 6px; background: var(--paper); }
  .badge--outlined .badge__fill {
    width: 100%; height: 100%; background: var(--navy);
    display: flex; align-items: center; justify-content: center;
  }
  .badge--framed { border: 5px solid var(--pale); }
  .badge .name { font-size: 14px; }
  .back2__mark {
    position: absolute; left: 216px; top: 96px;
    width: 76px; height: 76px; background: var(--pale);
  }
  .back2__name {
    position: absolute; left: 0; right: 0; top: 204px;
    text-align: center; font-size: 19px;
  }
</style>
</head>
<body>

  <div class="label" style="left:178px; top:50px;">Front</div>
  <div class="label" style="left:736px; top:50px;">Back - 1</div>
  <div class="label" style="left:178px; top:410px;">Back - 2</div>
  <div class="label" style="left:736px; top:410px;">Back - 3</div>

  <section class="card card--light" style="left:72px; top:90px;">
    <svg class="front__wave" width="508" height="290" viewBox="0 0 508 290" aria-hidden="true">
      <defs>
        <linearGradient id="bandGrad" x1="0" y1="0" x2="1" y2="0">
          <stop offset="0" stop-color="#164f86"/>
          <stop offset="1" stop-color="#2a8fd2"/>
        </linearGradient>
      </defs>
      <path d="M0 202 C120 195 220 230 330 250 C410 262 470 262 508 258 L508 290 L0 290 Z" fill="url(#bandGrad)"/>
      <path d="M0 200 C140 200 240 238 340 248 C420 255 480 240 508 230 L508 238 C470 252 410 262 330 255 C230 245 130 210 0 206 Z" fill="#0e2f52"/>
      <path d="M150 212 C260 232 360 245 430 238 C470 233 495 222 508 216 L508 226 C480 240 440 248 400 248 C320 248 240 232 150 212 Z" fill="#f39a22"/>
    </svg>
    <div class="front__brand">MoneyMendPlus</div>
    <div class="front__divider"></div>
    <ul class="front__contact">
      <li><b>p</b> : 555-318-6207</li>
      <li><b>f</b> : 555-294-7153</li>
      <li><b>e</b> : info@miravelllending.example</li>
      <li><b>w</b> : www.miravelllending.example</li>
    </ul>
    <address class="front__address">
      30871 Calloway Ln. B-22<br>Houston, TX 75419
    </address>
  </section>

  <section class="card card--light" style="left:622px; top:90px;">
    <div class="slogan">Balance, Renewed!</div>
    <div class="badge badge--outlined">
      <div class="badge__fill"><span class="name">Mira Vell Lending</span></div>
    </div>
    <div class="url">www.miravelllending.example</div>
  </section>

  <section class="card card--dark" style="left:75px; top:450px;">
    <div class="slogan">Balance, Renewed!</div>
    <div class="back2__mark"></div>
    <div class="back2__name name">Mira Vell Lending</div>
    <div class="url">www.miravelllending.example</div>
  </section>

  <section class="card card--dark" style="left:622px; top:450px;">
    <div class="slogan">Balance, Renewed!</div>
    <div class="badge badge--framed"><span class="name">Mira Vell Lending</span></div>
    <div class="url">www.miravelllending.example</div>
  </section>

</body>
</html>
```